"Tandem Mouthguards " Custom-made Mouthguard Business Website

We need an informational website for our mouthguard Business "Tandem Mouthguards". The logo is navy blue/lime green so want to have colour scheme that goes nicely with this - have uploaded our mouthguard flyer with some information we need to put into the website but I do have more information to put in there.

Target Market(s)

Sports clubs, sportspeople, parents and kids, schools

Industry/Entity Type

Dental, Custom-made Sports Mouthguards

Coding

Coded - Design and coding required

Number of Pages Required

5+ page

Font styles to use
Serif
Sans Serif

Colors
0054AA
0677BA
7BADD7
CADEEF
E8F1F8
0094D4
00A9DD
6FCCEA
C7EBF8
E9F6FB
00AB8E
00BBA5
67D7C9
C6EFE9
E9F9F6
59FF00
82FF00
B8FF75
E3FFCB
F4FFEA
FFF300
FFF600
FEFA6F
FFFEC7
FFFEE8
FFC000
F8CF3A
FAE287
FDF2CF
FEFAEE
F0912C
F2A743
F7CA91
FBE8D2
FDF5EE
EE7325
F08F49
F5BC92
FAE3D3
FDF4ED

Requirements
Must have
• I want drop down pages, not one scrolling page. Different pages for each heading . Content uploaded - We need a general home page with lots of pictures and info that I'll provide. A page each dedicated to 1) About Us 2) Why choose a custom mouthguard? 3) Gallery 4) Contact Us. Will need logos from "Velora"
Nice to have
• Mainly use greens and blues, but happy to pop in some yellow/oranges/red oranges if it looks good

```html
<!DOCTYPE html>
<html lang="en">
<head>
<meta charset="utf-8">
<title>Tandem Mouthguards – Photo Gallery</title>
<link href="https://fonts.googleapis.com/css2?family=Poppins:wght@400;500;600;700&family=Montserrat:wght@700;800&display=swap" rel="stylesheet">
<style>
:root{
  --navy:#0b2a6c;
  --navy-deep:#08245f;
  --teal:#137b70;
  --blue:#0c4c8a;
  --green:#3ab54a;
  --lime:#59c23a;
  --aqua:#22c7d2;
  --cta-green:#34c759;
  --white:#ffffff;
  --ink:#0b2a6c;
  --gold:#f4e02a;
}
*{box-sizing:border-box;margin:0;padding:0}
html,body{width:1200px;height:2610px;overflow:hidden;background:var(--white);font-family:"Poppins",sans-serif;color:var(--ink)}
.page{position:relative;width:1200px;height:2610px;overflow:hidden}

/* hero */
.hero{position:absolute;left:0;top:0;width:1200px;height:600px;background:linear-gradient(115deg,var(--teal) 0%,#0f6a80 35%,var(--blue) 65%,#0a3278 100%)}
.hero-curve{position:absolute;left:0;top:0;width:1200px;height:600px}
.brand-small{position:absolute;left:112px;top:22px;width:170px;color:var(--white);font-family:"Montserrat",sans-serif;font-weight:800;line-height:1;white-space:nowrap}
.brand-small .sub{font-size:9px;letter-spacing:.5px;display:flex;align-items:center;gap:5px}
.brand-small .sub i{width:7px;height:7px;border-radius:50%;background:var(--lime);display:inline-block}
.brand-small .name{font-size:22px;margin-top:6px}
.brand-small .name2{font-size:15px;margin-top:2px}
.nav{position:absolute;left:297px;top:37px;width:792px;height:44px;border-radius:22px;background:rgba(255,255,255,.14);display:flex;align-items:center;padding-left:22px}
.nav a{color:var(--white);font-size:12px;font-weight:600;text-decoration:none;margin-right:57px;letter-spacing:.3px;white-space:nowrap}
.nav a.active{color:var(--gold)}
.nav .contact{position:absolute;right:2px;top:2px;height:40px;width:152px;border-radius:20px;background:var(--green);display:flex;align-items:center;padding-left:22px;margin:0}
.nav .contact span{position:absolute;right:4px;top:4px;width:32px;height:32px;border-radius:50%;background:var(--navy);display:flex;align-items:center;justify-content:center}
.nav .contact span i{width:12px;height:12px;border-radius:50%;border:3px solid var(--white)}
.hero-brand{position:absolute;left:110px;top:170px;color:var(--white);font-family:"Montserrat",sans-serif;font-weight:800;white-space:nowrap}
.hero-brand .l1{font-size:80px;line-height:1;letter-spacing:2px}
.hero-brand .l2{font-size:31px;letter-spacing:8.6px;margin-top:16px;padding-bottom:8px;border-bottom:2px solid var(--green);width:400px}
.hero-title{position:absolute;left:114px;top:318px;font-size:38px;font-weight:600;color:var(--white)}
.hero-lead{position:absolute;left:114px;top:377px;font-size:14.5px;color:var(--white);white-space:nowrap}
.hero-art{position:absolute;left:528px;top:175px;width:600px;height:290px;border-radius:140px 140px 40px 40px;background:radial-gradient(circle at 45% 45%,#f3f0f5 0%,#e0354c 38%,#3d8be0 68%,rgba(20,70,140,0) 100%);opacity:.9}

/* gallery */
.gallery-title{position:absolute;left:0;top:648px;width:1200px;text-align:center;font-size:30px;font-weight:600;color:var(--navy)}
.gallery-title em{font-style:normal;color:var(--green)}
.grid{position:absolute;left:113px;top:710px;display:grid;grid-template-columns:repeat(3,317px);grid-template-rows:repeat(3,338px);column-gap:12px;row-gap:14px}
.tile{border:3px solid var(--navy);border-radius:10px;padding:3px;background:var(--white)}
.tile div{width:100%;height:100%;border-radius:6px}
.p1{background:linear-gradient(135deg,#d9c9c2,#8a5cc9)}
.p2{background:linear-gradient(135deg,#b7a7d8,#e07a96 50%,#3a78c7)}
.p3{background:linear-gradient(135deg,#a66a3d,#3a7ccc 50%,#9b6136)}
.p4{background:linear-gradient(135deg,#e7e4e0,#4bc45a 60%,#8fa367)}
.p5{background:linear-gradient(135deg,#d81d12,#7c2a16 45%,#ece8e6)}
.p6{background:linear-gradient(135deg,#3cc33e,#f4f5f6 50%,#4aa542)}
.p7{background:linear-gradient(135deg,#d83dd0,#5d3ee0 55%,#e457e0)}
.p8{background:linear-gradient(135deg,#3b7fc0,#163c56 50%,#4a90c9)}
.p9{background:linear-gradient(135deg,#8a6440,#f2f2f2 45%,#8e1c2d)}
.deco{position:absolute;border-radius:50%}
.deco-r{left:1130px;top:610px;width:140px;height:150px;background:linear-gradient(160deg,#d06bd6,#4fc9d8 50%,#7a4ed0)}
.deco-l{left:-70px;top:1700px;width:130px;height:140px;background:linear-gradient(160deg,#52c9c0,#f4f4f4 40%,#7a50c8)}
.pager{position:absolute;left:490px;top:1797px;display:flex;gap:6px}
.pager span{width:32px;height:32px;border-radius:50%;border:1px solid var(--navy);display:flex;align-items:center;justify-content:center;font-size:14px;color:var(--navy)}
.pager span.arrow{background:var(--navy);color:var(--white)}

/* call to action */
.big-word{position:absolute;left:0;top:1885px;width:1200px;text-align:center;font-family:"Montserrat",sans-serif;font-weight:700;font-size:88px;letter-spacing:1px;color:#e3f6ea;line-height:1;white-space:nowrap}
.cta{position:absolute;left:0;top:1968px;width:1200px;height:440px;background:linear-gradient(90deg,var(--aqua),var(--cta-green))}
.circle-photo{position:absolute;border-radius:50%;border:5px solid var(--white)}
.c1{left:198px;top:1888px;width:192px;height:192px;background:linear-gradient(135deg,#c8190f,#6a2a18 50%,#ece7e4)}
.c2{left:114px;top:1940px;width:122px;height:122px;border-color:var(--aqua);background:linear-gradient(135deg,#d43ed0,#5a3ce0)}
.c3{left:812px;top:2180px;width:190px;height:190px;background:linear-gradient(160deg,#3b80d0,#1c4c9a 60%,#9a6a45)}
.c4{left:956px;top:2230px;width:118px;height:118px;border-color:var(--cta-green);background:linear-gradient(135deg,#9b6be0,#4a2ea0)}
.cta-title{position:absolute;left:0;top:2012px;width:1200px;text-align:center;color:var(--white);font-size:38px;font-weight:600;line-height:46px}
.cta-text{position:absolute;left:0;top:2108px;width:1200px;text-align:center;color:var(--white);font-size:11.5px;line-height:16px}
.btn{position:absolute;left:525px;top:2164px;width:152px;height:44px;border:1.5px solid var(--white);border-radius:22px;color:var(--white);font-size:11.5px;font-weight:600;padding:13px 0 0 25px}
.btn span{position:absolute;right:4px;top:4px;width:34px;height:34px;border-radius:50%;background:var(--navy);display:flex;align-items:center;justify-content:center}
.btn span i{width:14px;height:14px;border-radius:50%;border:3px solid var(--white)}
.foot-curve{position:absolute;left:0;top:0;width:1200px;height:2610px;pointer-events:none}

/* footer */
.partner{position:absolute;left:0;top:2300px;width:1200px;text-align:center;color:var(--white);font-size:28px;font-weight:500;letter-spacing:1px;display:flex;justify-content:center;align-items:center;gap:10px}
.partner i{width:20px;height:20px;border-radius:50%;background:#f2d31d;display:inline-block}
.footer{position:absolute;left:0;top:2390px;width:1200px;height:220px;background:var(--navy-deep);color:var(--white)}
.f-brand{position:absolute;left:113px;top:18px;font-family:"Montserrat",sans-serif;font-weight:800;white-space:nowrap}
.f-brand .sub{font-size:13px;letter-spacing:.5px}
.f-brand .name{font-size:22px;margin-top:8px;line-height:1.05}
.f-note{position:absolute;left:113px;top:125px;font-size:9px;line-height:15px;width:160px}
.f-col{position:absolute;top:12px}
.f-col h4{font-size:14px;font-weight:600;margin-bottom:12px}
.f-col li{list-style:none;font-size:9px;margin-bottom:9px}
.links{left:402px}
.contact-col{left:627px}
.follow{left:968px}
.f-row{display:flex;align-items:center;gap:10px;font-size:9px;margin-bottom:13px}
.f-row b{width:22px;height:22px;border-radius:50%;border:1.5px solid var(--green);display:flex;align-items:center;justify-content:center}
.rule{position:absolute;left:113px;top:183px;width:975px;height:1px;background:rgba(255,255,255,.3)}
.copy{position:absolute;left:0;top:197px;width:1200px;text-align:center;font-size:9px}
</style>
</head>
<body>
<div class="page">

  <header class="hero">
    <svg class="hero-curve" viewBox="0 0 1200 600" aria-hidden="true">
      <path d="M0 462 Q600 672 1200 462 L1200 472 Q600 715 0 472 Z" fill="#0a2a6e"/>
      <path d="M0 472 Q600 715 1200 472 L1200 600 L0 600 Z" fill="#fff"/>
      <path d="M0 455 Q600 665 1200 455 L1200 462 Q600 672 0 462 Z" fill="#fff"/>
    </svg>
    <div class="brand-small">
      <div class="sub"><i></i>HARBOUR DENTURE CARE</div>
      <div class="name">TANDEM</div>
      <div class="name2">MOUTHGUARDS</div>
    </div>
    <nav class="nav">
      <a href="#">HOME</a>
      <a href="#">ABOUT US</a>
      <a href="#">OUR MOUTHGUARDS</a>
      <a href="#" class="active">PHOTO GALLERY</a>
      <a href="#">FAQ</a>
      <a href="#" class="contact">CONTACT US<span><i></i></span></a>
    </nav>
    <div class="hero-brand">
      <div class="l1">TANDEM</div>
      <div class="l2">MOUTHGUARDS</div>
    </div>
    <h1 class="hero-title">Our Gallery</h1>
    <p class="hero-lead">Explore our designs, colours, and real game-day smiles.</p>
    <div class="hero-art" role="img" aria-label="Colourful custom mouthguards and storage cases arranged in a group"></div>
  </header>

  <div class="deco deco-r" role="img" aria-label="Swirled multicolour mouthguard detail"></div>
  <h2 class="gallery-title">TANDEM MOUTHGUARDS PHOTO <em>GALLERY</em></h2>
  <section class="grid">
    <div class="tile"><div class="p1" role="img" aria-label="Purple glitter mouthguards held in a hand"></div></div>
    <div class="tile"><div class="p2" role="img" aria-label="Checkered and glitter mouthguards in a tub"></div></div>
    <div class="tile"><div class="p3" role="img" aria-label="Two blue glitter mouthguard blanks on wood"></div></div>
    <div class="tile"><div class="p4" role="img" aria-label="Green and purple mouthguard in a green case"></div></div>
    <div class="tile"><div class="p5" role="img" aria-label="Dark and pink mouthguards in red and white cases"></div></div>
    <div class="tile"><div class="p6" role="img" aria-label="White mouthguard with team emblem on a green case"></div></div>
    <div class="tile"><div class="p7" role="img" aria-label="Blue glitter mouthguard in a pink case"></div></div>
    <div class="tile"><div class="p8" role="img" aria-label="Dark galaxy glitter mouthguard on blue"></div></div>
    <div class="tile"><div class="p9" role="img" aria-label="School mouthguards in maroon and white in a white case"></div></div>
  </section>
  <div class="deco deco-l" role="img" aria-label="Striped multicolour mouthguard detail"></div>
  <div class="pager">
    <span class="arrow">&#8249;</span><span>1</span><span>2</span><span>3</span><span>4</span><span class="arrow">&#8250;</span>
  </div>

  <div class="big-word" aria-hidden="true">TANDEM MOUTHGUARDS</div>
  <section class="cta"></section>
  <svg class="foot-curve" viewBox="0 0 1200 2610" aria-hidden="true">
    <path d="M0 2380 Q600 2055 1200 2380 L1200 2390 Q600 2065 0 2390 Z" fill="#fff"/>
    <path d="M0 2395 Q600 2070 1200 2395 L1200 2610 L0 2610 Z" fill="#08245f"/>
  </svg>
  <div class="circle-photo c1" role="img" aria-label="Mouthguards in red and white cases"></div>
  <div class="circle-photo c2" role="img" aria-label="Blue glitter mouthguard"></div>
  <h2 class="cta-title">Now you’re<br>Ready for game day!</h2>
  <p class="cta-text">Our turnaround time is generally 1-2 weeks,&nbsp; however we may be able to<br>accommodate quicker turnaround times. Contact us for more details.</p>
  <a class="btn">BOOK NOW<span><i></i></span></a>
  <div class="circle-photo c3" role="img" aria-label="Blue glitter mouthguard blanks"></div>
  <div class="circle-photo c4" role="img" aria-label="Purple mouthguard in a case"></div>

  <div class="partner"><i></i>VELORA<i></i></div>

  <footer class="footer">
    <div class="f-brand">
      <div class="sub">HARBOUR DENTURE CARE</div>
      <div class="name">TANDEM<br>MOUTHGUARDS</div>
    </div>
    <p class="f-note">*Available to fund members with dental coverage</p>
    <div class="f-col links">
      <h4>MAIN LINKS</h4>
      <ul><li>Home</li><li>About US</li><li>Our Mouthguards</li><li>Photo Gallery</li><li>FAQ</li><li>Contact Us</li></ul>
    </div>
    <div class="f-col contact-col">
      <h4>CONTACT US</h4>
      <div class="f-row"><b><svg width="10" height="12" viewBox="0 0 10 12"><path d="M5 0C2.2 0 0 2.2 0 5c0 3.5 5 7 5 7s5-3.5 5-7C10 2.2 7.8 0 5 0zm0 7a2 2 0 110-4 2 2 0 010 4z" fill="#fff"/></svg></b>Unit 5/12 Coralline Way, Brookvale WA 6101</div>
      <div class="f-row"><b><svg width="11" height="11" viewBox="0 0 11 11"><path d="M2 0l2 2.5-1 1.5c.7 1.5 2 2.8 3.5 3.5l1.5-1L11 8.5 9.5 11C4.5 10.5.5 6.5 0 1.5z" fill="#fff"/></svg></b>08 5550 2718</div>
      <div class="f-row"><b><svg width="11" height="8" viewBox="0 0 11 8"><rect x=".5" y=".5" width="10" height="7" fill="none" stroke="#fff"/><path d="M.5.5l5 4 5-4" fill="none" stroke="#fff"/></svg></b>hello@harbourdenturecare.example</div>
    </div>
    <div class="f-col follow">
      <h4>FOLLOW US ON</h4>
      <div class="f-row"><b></b>Chatter</div>
      <div class="f-row"><b></b>Chirper</div>
      <div class="f-row"><b></b>Worklink</div>
    </div>
    <div class="rule"></div>
    <p class="copy">©2025 Tandem Mouthguards All Rights Reserved.</p>
  </footer>

</div>
</body>
</html>
```